Corvane Capital Business Cards

These are professional business cards that are for my family office.
Put fake emails and phone numbers as of now until I finalize those components. This family office controls my families investments, assets, and future. The cards should be professional.
..
.
.
.
I just uploaded another variation of a logo I would like to see as a business card to I am inbeteen which logo to use

Target Market(s)

business

Industry/Entity Type

business

Contact Information for Business Card

Professional, wealth related, finance related.

Requirements
Must have
• Logo

```html
<!DOCTYPE html>
<html lang="en">
<head>
<meta charset="utf-8">
<title>Corvane Capital Business Cards</title>
<link rel="stylesheet" href="https://fonts.googleapis.com/css2?family=Cinzel:wght@600&family=Montserrat:wght@400;500;700&display=swap">
<style>
  :root {
    --backdrop: #3b3c3e;
    --card: #f1f1f1;
    --ink: #141a2b;
    --ink-soft: #2a2f3d;
  }
  * { margin: 0; padding: 0; box-sizing: border-box; }
  html, body {
    width: 1200px;
    height: 1059px;
    overflow: hidden;
    background: var(--backdrop);
  }
  .canvas {
    position: relative;
    width: 1200px;
    height: 1059px;
  }
  .card {
    position: absolute;
    background: var(--card);
    border-radius: 20px;
    color: var(--ink);
  }
  .card--front { left: 256px; top: 100px; width: 688px; height: 392px; }
  .card--back  { left: 253px; top: 536px; width: 694px; height: 396px; }

  .company-name {
    position: absolute;
    font-family: "Cinzel", serif;
    font-weight: 600;
    color: var(--ink);
    white-space: nowrap;
    line-height: 1;
  }
  .card--front .company-name {
    left: 0; right: 0; top: 38px;
    text-align: center;
    font-size: 40px;
  }
  .card--back .company-name {
    left: 0; right: 0; top: 298px;
    text-align: center;
    font-size: 40px;
  }

  .holder {
    position: absolute;
    right: 356px;
    top: 164px;
    text-align: right;
    font-family: "Montserrat", sans-serif;
    white-space: nowrap;
  }
  .holder__name {
    font-weight: 700;
    font-size: 31px;
    line-height: 1;
    letter-spacing: 0.2px;
  }
  .holder__role {
    margin-top: 9px;
    font-weight: 400;
    font-size: 18px;
    line-height: 1;
    color: var(--ink-soft);
  }

  .divider {
    position: absolute;
    left: 358px;
    top: 161px;
    width: 2px;
    height: 71px;
    background: var(--ink);
  }

  .contacts {
    position: absolute;
    left: 393px;
    top: 157px;
    list-style: none;
    font-family: "Montserrat", sans-serif;
    font-size: 18.5px;
    color: var(--ink-soft);
  }
  .contacts li {
    display: flex;
    align-items: center;
    height: 27px;
    white-space: nowrap;
  }
  .contacts svg {
    width: 14px;
    height: 14px;
    margin-right: 9px;
    fill: var(--ink);
    flex: none;
  }

  .address {
    position: absolute;
    left: 0; right: 0; top: 347px;
    text-align: center;
    font-family: "Montserrat", sans-serif;
    font-size: 17px;
    color: var(--ink-soft);
    white-space: nowrap;
  }

  .brand-circle {
    position: absolute;
    left: 246px;
    top: 63px;
    width: 206px;
    height: 206px;
    border: 3px solid var(--ink);
    border-radius: 50%;
  }
</style>
</head>
<body>
<main class="canvas">

  <section class="card card--front" aria-label="Business card front">
    <h1 class="company-name">Corvane Capital</h1>

    <div class="holder">
      <p class="holder__name">DANIEL HARTLEY</p>
      <p class="holder__role">Managing Director</p>
    </div>

    <div class="divider"></div>

    <ul class="contacts">
      <li>
        <svg viewBox="0 0 16 16" aria-hidden="true"><path d="M1 6c0-2 3-4 7-4s7 2 7 4v1h-3.5V5.5h-7V7H1z M3.5 8.5 5 7h6l1.5 1.5V14h-9z"/><circle cx="8" cy="10.5" r="1.8" fill="#f1f1f1"/></svg>
        <span>123 456 789</span>
      </li>
      <li>
        <svg viewBox="0 0 16 16" aria-hidden="true"><path d="M1 3.5h14v1.2L8 9 1 4.7z M1 6.4l7 4.3 7-4.3V13H1z"/></svg>
        <span>info@corvanemail.com</span>
      </li>
      <li>
        <svg viewBox="0 0 16 16" aria-hidden="true"><circle cx="8" cy="8" r="7"/><path d="M4 4.5c1 0 2 1 1.5 2S7 8 6.5 9 5 10 5 12c-1-1-2.5-2.5-2.5-4S3 5 4 4.5z M9.5 2.5c1 1 0 2 1 2.5s2 0 2.5 1.5c-1 .5-2 1-2.5 2s.5 2-.5 3.5c-.5-1-1-2-1.5-3S7.5 7 8 6s1-2.5 1.5-3.5z" fill="#f1f1f1"/></svg>
        <span>www.corvanecapital.com</span>
      </li>
    </ul>

    <p class="address">Your address, City State, Zip 1234</p>
  </section>

  <section class="card card--back" aria-label="Business card back">
    <div class="brand-circle" aria-hidden="true"></div>
    <h2 class="company-name">Corvane Capital</h2>
  </section>

</main>
</body>
</html>
```